Redesign of business card for Cedar Ridge Mechanical

We are looking for a new design for our business cards for Cedar Ridge Mechanical. We are a plumbing & HVAC construction company, operating on the West Coast of Canada and USA. Logo attached.
Industry/Entity Type
Construction - Plumbing & HVAC
Contact Information for Business Card
Name, address, phone numbers, email, website address
Look and feel
Each slider illustrates characteristics of the customer's brand and the style your logo design should communicate.

```html
<!DOCTYPE html>
<html lang="en">
<head>
<meta charset="utf-8">
<title>Cedar Ridge Mechanical – Business Card</title>
<link href="https://fonts.googleapis.com/css2?family=Montserrat:wght@400;500;600;700&display=swap" rel="stylesheet">
<style>
  :root {
    --ink: #141414;
    --paper: #ffffff;
    --stage: #dedfe1;
    --muted: #3a3a3a;
    --rule: #1c1c1c;
  }
  * { box-sizing: border-box; margin: 0; padding: 0; }
  html, body {
    width: 1200px; height: 900px; overflow: hidden;
    background: var(--stage);
    font-family: "Montserrat", sans-serif;
  }
  .canvas {
    position: relative; width: 1200px; height: 900px;
    display: flex; flex-direction: column; align-items: center; justify-content: center; gap: 60px;
  }
  .card {
    position: relative; width: 560px; height: 320px;
    border-radius: 26px; overflow: hidden;
    box-shadow: 0 6px 18px rgba(0,0,0,.18);
  }
  /* Front */
  .card-front { background: var(--paper); color: var(--ink); }
  .card-front .band { position: absolute; inset: 0; width: 100%; height: 100%; }
  .brand {
    position: absolute; display: flex; align-items: center; gap: 10px;
    font-weight: 600; text-transform: uppercase; letter-spacing: .04em;
  }
  .brand-square { width: 14px; height: 14px; background: currentColor; flex: none; }
  .card-front .brand {
    left: 34px; top: 72px; width: 200px; font-size: 17px; line-height: 1.25; color: var(--ink);
  }
  .divider {
    position: absolute; left: 252px; top: 60px; width: 1.5px; height: 150px; background: var(--rule);
  }
  .contact { position: absolute; left: 272px; top: 58px; }
  .contact .name { font-size: 22px; font-weight: 700; line-height: 1.1; }
  .contact .role { font-size: 13px; font-weight: 400; color: var(--muted); margin-top: 3px; }
  .contact .address { font-size: 12.5px; color: var(--muted); line-height: 1.35; margin-top: 6px; }
  .contact ul { list-style: none; margin-top: 6px; }
  .contact li {
    display: flex; align-items: center; gap: 9px;
    font-size: 12.5px; color: var(--muted); line-height: 1.7;
  }
  .contact li svg { width: 11px; height: 11px; flex: none; fill: var(--ink); }
  /* Back */
  .card-back { background: var(--ink); color: var(--paper); display: flex; align-items: center; justify-content: center; }
  .card-back .brand { position: static; font-size: 24px; gap: 14px; }
  .card-back .brand-square { width: 20px; height: 20px; }
</style>
</head>
<body>
<main class="canvas">
  <section class="card card-front" aria-label="Business card front">
    <svg class="band" viewBox="0 0 560 320" preserveAspectRatio="none" aria-hidden="true">
      <path d="M0 232 C 160 262, 360 296, 560 300 L560 320 L0 320 Z" fill="#141414"/>
      <path d="M40 222 C 200 252, 380 278, 548 282" fill="none" stroke="#141414" stroke-width="2.5" stroke-linecap="round"/>
    </svg>
    <div class="brand"><span class="brand-square"></span><span>Cedar Ridge Mechanical</span></div>
    <div class="divider"></div>
    <div class="contact">
      <p class="name">Daniel Hart</p>
      <p class="role">Managing Director</p>
      <p class="address">240 Harbor View Road<br>Bellevue, WA 98004</p>
      <ul>
        <li><svg viewBox="0 0 24 24"><path d="M6.6 10.8a15.1 15.1 0 0 0 6.6 6.6l2.2-2.2a1 1 0 0 1 1-.25 11.4 11.4 0 0 0 3.6.57 1 1 0 0 1 1 1V20a1 1 0 0 1-1 1A17 17 0 0 1 3 4a1 1 0 0 1 1-1h3.5a1 1 0 0 1 1 1c0 1.25.2 2.45.57 3.57a1 1 0 0 1-.25 1z"/></svg>555.210.4471</li>
        <li><svg viewBox="0 0 24 24"><path d="M2 5h20v14H2z M4 7v.5l8 5 8-5V7z" fill-rule="evenodd"/></svg>info@cedarridgemech.com</li>
        <li><svg viewBox="0 0 24 24"><circle cx="12" cy="12" r="10"/></svg>www.cedarridgemech.com</li>
      </ul>
    </div>
  </section>

  <section class="card card-back" aria-label="Business card back">
    <div class="brand"><span class="brand-square"></span><span>Cedar Ridge Mechanical</span></div>
  </section>
</main>
</body>
</html>
```